Business cards for Harbourline Supply Pty Ltd that import building products into Australia from China
Target Market(s)
Business to Business
Industry/Entity Type
Business
Contact Information for Business Card
Front: Logo and Business Name
Rear:
Desmond Varrick
General Manager
Mobile: 0427 561 394
email: dessie@harbourlinesupply.com.au
alternative email: dessie@outbackworks.com.au
web: www.harbourlinesupply.com.au
Adelaide, Brisbane and Darwin
Colors
ec1f27
fbee3d

```html
<!DOCTYPE html>
<html lang="en">
<head>
<meta charset="utf-8">
<title>Harbourline Supply Pty Ltd — Business Cards</title>
<link href="https://fonts.googleapis.com/css2?family=Lato:wght@400;700;900&display=swap" rel="stylesheet">
<style>
  :root {
    --brand-red: #ec1f27;
    --brand-yellow: #fbee3d;
    --ink: #2b2b2b;
    --paper: #ffffff;
    --backdrop: #e6e6e6;
    --mark-grey: #4a4a4a;
  }
  * { margin: 0; padding: 0; box-sizing: border-box; }
  html, body {
    width: 1200px; height: 900px; overflow: hidden;
    background: var(--backdrop);
    font-family: "Lato", sans-serif;
  }
  .canvas { position: relative; width: 1200px; height: 900px; }

  .card {
    position: absolute;
    overflow: hidden;
    box-shadow: 0 14px 30px rgba(0,0,0,0.18);
  }

  /* Front card */
  .card--front {
    left: 570px; top: 90px; width: 560px; height: 320px;
    background: var(--brand-red);
    display: flex; flex-direction: column; align-items: center; justify-content: center;
    gap: 26px;
  }
  .brand {
    display: flex; align-items: center; gap: 14px;
    font-weight: 900; letter-spacing: -0.5px; white-space: nowrap;
  }
  .brand__dot { border-radius: 50%; flex: none; }
  .card--front .brand { color: var(--paper); font-size: 28px; }
  .card--front .brand__dot { width: 40px; height: 40px; background: var(--brand-yellow); }
  .card--front .web { color: var(--paper); font-size: 17px; letter-spacing: 0.6px; }

  /* Rear card */
  .card--rear {
    left: 70px; top: 430px; width: 640px; height: 366px;
    background: var(--paper);
  }
  .card--rear .brand {
    position: absolute; left: 44px; top: 42px;
    color: var(--brand-red); font-size: 27px;
  }
  .card--rear .brand__dot { width: 38px; height: 38px; background: var(--mark-grey); }
  .rule {
    position: absolute; left: 44px; right: 0; top: 118px;
    height: 2px; background: var(--brand-red);
  }
  .contacts {
    position: absolute; left: 44px; top: 138px;
    list-style: none; color: var(--ink); font-size: 15px; line-height: 24px;
  }
  .contacts li { display: flex; align-items: center; gap: 9px; }
  .contacts svg { width: 13px; height: 13px; flex: none; }

  .person {
    position: absolute; right: 44px; top: 140px; text-align: right; color: var(--ink);
  }
  .person__name { color: var(--brand-red); font-weight: 700; font-size: 26px; }
  .person__role { font-size: 17px; margin-top: 2px; }
  .person__address { font-size: 17px; line-height: 22px; margin-top: 24px; }

  .band-yellow {
    position: absolute; left: 0; bottom: 0; width: 300px; height: 26px;
    background: var(--brand-yellow);
  }
  .band-red {
    position: absolute; right: 0; bottom: 0; width: 370px; height: 52px;
    background: var(--brand-red); border-top-left-radius: 36px;
    display: flex; align-items: center; justify-content: center;
  }
  .band-red .web { color: var(--paper); font-size: 17px; letter-spacing: 0.6px; }
</style>
</head>
<body>
<div class="canvas">

  <section class="card card--front">
    <div class="brand"><span class="brand__dot"></span>Harbourline Supply Pty Ltd</div>
    <p class="web">www.harbourlinesupply.com.au</p>
  </section>

  <section class="card card--rear">
    <div class="brand"><span class="brand__dot"></span>Harbourline Supply Pty Ltd</div>
    <div class="rule"></div>

    <ul class="contacts">
      <li>
        <svg viewBox="0 0 12 12" aria-hidden="true"><rect x="3" y="0.5" width="6" height="11" rx="1" fill="none" stroke="var(--brand-red)" stroke-width="1.2"/><rect x="4.2" y="2" width="3.6" height="6" fill="var(--brand-red)"/></svg>
        0427 561 394
      </li>
      <li>
        <svg viewBox="0 0 12 12" aria-hidden="true"><rect x="0.5" y="2" width="11" height="8" fill="var(--brand-red)"/><path d="M0.5 2 L6 6.5 L11.5 2" fill="none" stroke="#fff" stroke-width="1"/></svg>
        dessie@harbourlinesupply.com.au
      </li>
      <li>
        <svg viewBox="0 0 12 12" aria-hidden="true"><rect x="0.5" y="2" width="11" height="8" fill="var(--brand-red)"/><path d="M0.5 2 L6 6.5 L11.5 2" fill="none" stroke="#fff" stroke-width="1"/></svg>
        dessie@outbackworks.com.au
      </li>
    </ul>

    <div class="person">
      <p class="person__name">Desmond Varrick</p>
      <p class="person__role">General Manager</p>
      <p class="person__address">1450 Marlow Lane<br>Kestrel TX 78100</p>
    </div>

    <div class="band-yellow"></div>
    <div class="band-red"><p class="web">www.harbourlinesupply.com.au</p></div>
  </section>

</div>
</body>
</html>
```